Business card design for new eCommerce site focusing on integrity and strong businsess tactics

We need a business card that will stand out and be memorable. Something with color that matches our company logo colors. Think high end version of Pactivo. There are 2 logos provided. The parent company is called Amber Ledge Partners and we are presenting a new and very exciting eCommerce site called BrightHarborTrade.example.

Target Market(s)

Our target markets are in the Activities, Food and Beverage, Health and Beauty

Industry/Entity Type

Marketing

Contact Information for Business Card

We have 4 members that need cards...I will provide all info to the winner of the design contest
Business Address is
4870 West 63rd Avenue, Suite C207
Phoenix AZ 85731

Font styles to use
Serif
Sans Serif

Colors

Designer to choose colors to be used in the design.

Requirements
Must have
• The card must be memorable...should be unique in design but must exude integrity and be playful .
• I have provided several colors or our parent company...please feel free to use which ever
Nice to have
• I will leave this up to you. Feel free to use other images of your choosing that wraps around our client.....Activities, Dining, Health, Beauty
Should not have
• just dont be boring

```html
<!DOCTYPE html>
<html lang="en">
<head>
<meta charset="utf-8">
<title>Business Cards – Amber Ledge Partners / BrightHarborTrade</title>
<link rel="stylesheet" href="https://fonts.googleapis.com/css2?family=Montserrat:wght@700&family=Mulish:wght@400;600;700&display=swap">
<style>
  :root {
    --backdrop: #3a3a3c;
    --brand-blue: #1f7db8;
    --accent-blue: #2a77b5;
    --accent-green: #7dc242;
    --card-white: #ffffff;
    --ink-grey: #6b6b6b;
    --faint-blue: #eef0f6;
  }
  * { margin: 0; padding: 0; box-sizing: border-box; }
  html, body { width: 1200px; height: 810px; overflow: hidden; }
  body {
    background: var(--backdrop);
    position: relative;
    font-family: "Mulish", Arial, sans-serif;
  }
  .card {
    position: absolute;
    width: 560px;
    height: 320px;
    overflow: hidden;
    box-shadow: 0 8px 24px rgba(0,0,0,0.35);
  }

  /* Front: parent company */
  .card--parent {
    left: 80px; top: 70px;
    background: var(--brand-blue);
    color: var(--card-white);
    text-align: center;
  }
  .parent-mark {
    position: absolute;
    left: 50%; top: 62px;
    width: 62px; height: 62px;
    margin-left: -31px;
    border: 4px solid var(--card-white);
    border-radius: 50%;
  }
  .parent-name {
    position: absolute;
    left: 0; right: 0; top: 150px;
    font-family: "Montserrat", Arial, sans-serif;
    font-weight: 700;
    font-size: 34px;
    letter-spacing: 0.5px;
  }
  .parent-web {
    position: absolute;
    left: 0; right: 0; top: 236px;
    font-size: 12px;
    letter-spacing: 1.6px;
  }

  /* Back: eCommerce site */
  .card--site {
    left: 560px; top: 430px;
    background: var(--card-white);
  }
  .site-watermark {
    position: absolute;
    left: 60px; top: 40px;
    width: 170px; height: 170px;
    border-radius: 50%;
    background: var(--faint-blue);
  }
  .site-logo {
    position: absolute;
    right: 40px; top: 34px;
    text-align: left;
  }
  .site-logo__row { display: flex; align-items: center; gap: 8px; }
  .site-logo__dot {
    width: 18px; height: 18px; border-radius: 50%;
    background: var(--accent-blue);
  }
  .site-logo__name {
    font-weight: 700;
    font-size: 22px;
    color: var(--accent-green);
  }
  .site-logo__tagline {
    margin-left: 26px;
    font-size: 10.5px;
    letter-spacing: 0.8px;
    color: var(--ink-grey);
  }
  .rule {
    position: absolute;
    height: 1.5px;
    background: var(--accent-green);
  }
  .rule--top { left: 250px; right: 30px; top: 120px; }
  .rule--mid { left: 50px; right: 30px; top: 232px; }
  .side-tab {
    position: absolute;
    left: 0; top: 200px;
    width: 12px; height: 34px;
    background: var(--accent-green);
  }
  .holder {
    position: absolute;
    left: 50px; top: 180px;
  }
  .holder__name {
    font-weight: 700;
    font-size: 20px;
    color: var(--accent-blue);
    line-height: 1.1;
  }
  .holder__role {
    font-size: 16px;
    color: var(--ink-grey);
  }
  .contact {
    position: absolute;
    left: 50px; top: 244px;
    font-size: 12.5px;
    line-height: 1.75;
    color: var(--ink-grey);
  }
  .footer-band {
    position: absolute;
    left: 0; right: 0; bottom: 0;
    height: 10px;
    display: flex;
  }
  .footer-band__green { flex: 0 0 62%; background: var(--accent-green); }
  .footer-band__blue { flex: 1; background: var(--accent-blue); }
</style>
</head>
<body>

  <section class="card card--parent" aria-label="Amber Ledge Partners card front">
    <div class="parent-mark"></div>
    <h1 class="parent-name">Amber Ledge Partners</h1>
    <p class="parent-web">www.amberledgepartners.example</p>
  </section>

  <section class="card card--site" aria-label="BrightHarborTrade card back">
    <div class="site-watermark"></div>

    <div class="site-logo">
      <div class="site-logo__row">
        <span class="site-logo__dot"></span>
        <span class="site-logo__name">BrightHarborTrade.example</span>
      </div>
      <p class="site-logo__tagline">Activities-Dining-Health-Beauty</p>
    </div>

    <div class="rule rule--top"></div>

    <div class="side-tab"></div>
    <div class="holder">
      <p class="holder__name">Dana Whitlow</p>
      <p class="holder__role">Founder</p>
    </div>

    <div class="rule rule--mid"></div>

    <div class="contact">
      <p>Cell: 0400 555 019 | Email: info@brightharbortrade.example | Web: www.brightharbortrade.example</p>
      <p>4870 West 63rd Avenue, Suite C207 Phoenix AZ 85731</p>
    </div>

    <div class="footer-band">
      <span class="footer-band__green"></span>
      <span class="footer-band__blue"></span>
    </div>
  </section>

</body>
</html>
```